Simple landing page for Brambles cookbook

I need a one page landingpage where customers can order the cookbook.
This is a cookbook of a collection of recipes from our deli that we used to run.
I need a landing page where customers can come and order the book. I also need it coded. I already have the domain through hostwell.
I can send the file of the book through wetransfer. It's too big to upload here. Just so you get the feel that I am looking for.
I attached a simple text as an introduction to the page. But I am open to any suggestions. I want it all to be about the experience that we are sharing the recipes with everybody and that it's for sale. The book is $29.99, shipping included.
Customers have to be able to click and buy the book from it.

Coding

Coded - Design and coding required

Number of Pages Required

1 page

Font styles to use
Sans Serif

Requirements
Must have
• Same colors as the cookbook

```html
<!DOCTYPE html>
<html lang="en">
<head>
<meta charset="utf-8">
<title>Brambles Cookbook</title>
<link href="https://fonts.googleapis.com/css2?family=Poppins:wght@700&family=Roboto+Condensed:wght@400;700&family=Lato:wght@400&family=Roboto:wght@400&display=swap" rel="stylesheet">
<style>
:root{
  --pink:#e0185e;
  --brown:#4b2d25;
  --ink:#141414;
  --white:#ffffff;
  --black:#000000;
  --rule:#3a3a3a;
}
*{margin:0;padding:0;box-sizing:border-box}
html,body{width:888px;height:1200px;overflow:hidden;background:var(--white)}
body{position:relative;font-family:'Lato',sans-serif;color:var(--ink)}
.hero{position:absolute;left:0;top:0;width:888px;height:475px;overflow:hidden}
.hero-photo{position:absolute;inset:0;background:
  radial-gradient(ellipse 260px 200px at 600px 250px,#b07a45 0%,#8a5a33 40%,rgba(140,100,70,0) 100%),
  linear-gradient(180deg,#6e625a 0%,#9a918b 35%,#d9d6d3 70%,#e6e3e0 100%)}
.hero-shade{position:absolute;inset:0;background:linear-gradient(90deg,rgba(40,30,25,.45) 0%,rgba(40,30,25,.15) 55%,rgba(0,0,0,0) 100%)}
.nav{position:absolute;top:0;left:0;width:888px;height:72px}
.brand{position:absolute;left:110px;top:18px;font-family:'Poppins',sans-serif;font-weight:700;font-size:28px;color:var(--white);letter-spacing:-.5px}
.nav-links{position:absolute;left:258px;top:28px;display:flex;gap:34px;font-family:'Roboto Condensed',sans-serif;font-size:11.5px;color:var(--white);text-transform:uppercase}
.nav-links .active{color:var(--pink)}
.nav-phone{position:absolute;left:523px;top:24px;display:flex;align-items:center;gap:8px;font-family:'Roboto',sans-serif;font-size:12.5px;color:var(--white)}
.nav-phone .dot{width:23px;height:23px;border-radius:50%;background:var(--pink);display:flex;align-items:center;justify-content:center}
.login{position:absolute;left:687px;top:19px;width:91px;height:34px;background:var(--pink);color:var(--white);font-family:'Roboto Condensed',sans-serif;font-weight:700;font-size:12.5px;display:flex;align-items:center;justify-content:center;gap:8px;border-radius:2px}
.hero-copy{position:absolute;left:80px;top:172px;color:var(--white)}
.hero-title{font-family:'Poppins',sans-serif;font-weight:700;font-size:29px;line-height:42px;text-transform:uppercase}
.hero-sub{margin-top:10px;font-size:14px;line-height:19px;width:300px}
.btn{display:inline-flex;align-items:center;gap:9px;font-family:'Roboto Condensed',sans-serif;font-weight:700;font-size:11.5px;color:var(--white);text-transform:uppercase;border-radius:2px;padding:0 14px;height:35px}
.hero-copy .btn{margin-top:20px;background:var(--pink)}
.slides{position:absolute;left:832px;top:235px;font-family:'Roboto',sans-serif;font-size:12.5px;line-height:22px;color:var(--ink)}
.slides .current{color:var(--pink)}
.intro{position:absolute;left:0;top:475px;width:888px;height:552px}
.book-cover{position:absolute;left:108px;top:60px;width:260px;height:420px;background:linear-gradient(160deg,#eef4f8 0%,#dce8ef 40%,#b98a58 60%,#c5cdd2 100%);box-shadow:-6px 6px 18px rgba(0,0,0,.15);border-left:10px solid #e9ecee}
.intro-text{position:absolute;left:455px;top:70px;width:340px}
.intro-title{font-family:'Roboto Condensed',sans-serif;font-weight:700;font-size:26px;color:var(--ink)}
.price{margin-top:12px;font-family:'Roboto Condensed',sans-serif;font-weight:700;font-size:15px;color:var(--pink)}
.intro-text p{font-size:10.8px;line-height:17px;margin-top:9px;color:#222}
.intro-text .price+p{margin-top:12px}
.intro-text .btn{margin-top:16px;background:var(--brown)}
.footer{position:absolute;left:0;top:1027px;width:888px;height:173px;background:var(--black);color:var(--white);font-family:'Roboto',sans-serif}
.foot-nav{position:absolute;top:16px;width:100%;display:flex;justify-content:center;gap:36px;font-size:11.5px;text-transform:uppercase}
.foot-rule{position:absolute;left:82px;top:49px;width:724px;height:1px;background:var(--rule)}
.foot-brand{position:absolute;left:84px;top:70px;font-family:'Poppins',sans-serif;font-weight:700;font-size:28px;letter-spacing:-.5px}
.copyright{position:absolute;left:84px;top:125px;font-size:10px}
.foot-col{position:absolute;top:70px;font-size:11.5px}
.foot-col h4{font-family:'Roboto Condensed',sans-serif;font-weight:700;font-size:11.5px;text-transform:uppercase;margin-bottom:12px}
.foot-col .row{display:flex;gap:10px;align-items:flex-start;line-height:16px;margin-bottom:10px}
.loc{left:328px;width:190px}
.contact{left:549px}
.socials{position:absolute;left:748px;top:68px;display:grid;grid-template-columns:24px 24px;gap:8px}
.socials span{width:24px;height:24px;border:1.5px solid var(--white)}
</style>
</head>
<body>
<header class="hero">
  <div class="hero-photo" role="img" aria-label="Photo of a pulled meat sandwich with pickled onion and lettuce on a wooden board"></div>
  <div class="hero-shade"></div>
  <nav class="nav">
    <div class="brand">Brambles</div>
    <div class="nav-links"><span class="active">Home</span><span>Introduction</span><span>Contact Us</span></div>
    <div class="nav-phone"><span class="dot"><svg width="11" height="11" viewBox="0 0 24 24"><path fill="#fff" d="M6.6 10.8a15 15 0 0 0 6.6 6.6l2.2-2.2c.3-.3.7-.4 1-.2 1.1.4 2.3.6 3.6.6.6 0 1 .4 1 1V20c0 .6-.4 1-1 1A17 17 0 0 1 3 4c0-.6.4-1 1-1h3.5c.6 0 1 .4 1 1 0 1.3.2 2.5.6 3.6.1.3 0 .7-.2 1z"/></svg></span>+1 888 888 8888</div>
    <div class="login">LOGIN <svg width="9" height="11" viewBox="0 0 18 22"><rect x="1" y="9" width="16" height="12" rx="2" fill="#fff"/><path d="M4.5 9V6a4.5 4.5 0 0 1 9 0v3" fill="none" stroke="#fff" stroke-width="2.5"/></svg></div>
  </nav>
  <div class="hero-copy">
    <h1 class="hero-title">Welcome to<br>Brambles Cookbook</h1>
    <p class="hero-sub">We spent five years with this business until it’s eventual closure in April of 2015.</p>
    <a class="btn">Get Started <svg width="11" height="11" viewBox="0 0 20 20"><circle cx="10" cy="10" r="10" fill="#fff"/><path d="M8 5l5 5-5 5" fill="none" stroke="#e0185e" stroke-width="2.6"/></svg></a>
  </div>
  <div class="slides"><div class="current">01</div><div>02</div><div>03</div></div>
</header>

<section class="intro">
  <div class="book-cover" role="img" aria-label="Brambles Sandwiches cookbook cover with a ham and salami sandwich"></div>
  <div class="intro-text">
    <h2 class="intro-title">INTRODUCTION</h2>
    <div class="price">The book is $29.99,</div>
    <p>Opening it’s doors in January of 2010, Brambles European Deli was a sandwich shop in Alderport, Northbrook, but also a lot more than that.</p>
    <p>We spent five years with this business until it’s eventual closure in April of 2015. It was a special time where we met tons of amazing people, who we loved to see and serve.</p>
    <p>Brambles started out as a deli but eventually morphed into the sandwich shop we all know it as today.</p>
    <p>We are overwhelmed with the continuous positive messages and comments we get on our Chatterbox page that is still up and running.</p>
    <p>Unfortunately, we can’t open another Brambles, but we can offer you this collection of our recipes for you to try out at home with your family and friends</p>
    <p>If you do, please post your pictures of you making a meal or the finished product, or even enjoying it!</p>
    <a class="btn">Buy the Book <svg width="11" height="11" viewBox="0 0 20 20"><circle cx="10" cy="10" r="10" fill="#fff"/><path d="M8 5l5 5-5 5" fill="none" stroke="#4b2d25" stroke-width="2.6"/></svg></a>
  </div>
</section>

<footer class="footer">
  <div class="foot-nav"><span>Home</span><span>Introduction</span><span>Contact Us</span></div>
  <div class="foot-rule"></div>
  <div class="foot-brand">Brambles</div>
  <div class="copyright">©&nbsp; 2022 Brambles Cookbook All Right Reserved.</div>
  <div class="foot-col loc">
    <h4>Location</h4>
    <div class="row"><svg width="9" height="12" viewBox="0 0 18 24"><path fill="#fff" d="M9 0a9 9 0 0 0-9 9c0 7 9 15 9 15s9-8 9-15a9 9 0 0 0-9-9zm0 12a3 3 0 1 1 0-6 3 3 0 0 1 0 6z"/></svg><span>12,Lorem idm dolor consectetur adipiscing elitd sed do eiusmod</span></div>
  </div>
  <div class="foot-col contact">
    <h4>Contact Us</h4>
    <div class="row"><svg width="12" height="12" viewBox="0 0 24 24"><path fill="#fff" d="M6.6 10.8a15 15 0 0 0 6.6 6.6l2.2-2.2c.3-.3.7-.4 1-.2 1.1.4 2.3.6 3.6.6.6 0 1 .4 1 1V20c0 .6-.4 1-1 1A17 17 0 0 1 3 4c0-.6.4-1 1-1h3.5c.6 0 1 .4 1 1 0 1.3.2 2.5.6 3.6.1.3 0 .7-.2 1z"/></svg><span>+1 888 888 8888</span></div>
    <div class="row"><svg width="12" height="10" viewBox="0 0 24 18"><rect width="24" height="18" rx="2" fill="#fff"/><path d="M1 2l11 8 11-8" fill="none" stroke="#000" stroke-width="2"/></svg><span>info@bramblescookbook.com</span></div>
  </div>
  <div class="socials"><span></span><span></span><span></span><span></span></div>
</footer>
</body>
</html>
```